VENTURE CAPITAL GROUP BUSINESS CARD DESIGN

Venture Capital Group based in SF looking for a bold business card design. No trendy colour explosion, 3D effects etc. Just "simple" optical effects. Works on your brain, keeps your eye focused and sticks to your mind.
Target Market(s)
Technology startups
Industry/Entity Type
Venture Capital
Contact Information for Business Card
DESMOND WHITLAKE
MANAGING PARTNER
187 FENWORTH ST SAN FRANCISCO, CA 94187
415.555.0142 O
415.555.0147 F
415.555.0193 C
desmond@veldtmoorcapital.ventures

```html
<!DOCTYPE html>
<html lang="en">
<head>
<meta charset="utf-8">
<title>Veldtmoor Capital Group – Business Card</title>
<link rel="stylesheet" href="https://fonts.googleapis.com/css2?family=Open+Sans:wght@400;600;800&display=swap">
<style>
  :root {
    --green-deep: #0f5a2b;
    --green-card: #0e5a27;
    --green-bright: #3aa845;
    --grey-panel: #c9cacc;
    --white: #ffffff;
    --backdrop: #e6e7e8;
  }
  * { margin: 0; padding: 0; box-sizing: border-box; }
  html, body { width: 1200px; height: 900px; overflow: hidden; }
  body {
    background: var(--backdrop);
    font-family: "Open Sans", Arial, sans-serif;
    display: flex;
    flex-direction: column;
    align-items: center;
    justify-content: center;
    gap: 36px;
  }
  .card {
    position: relative;
    width: 700px;
    height: 400px;
    border-radius: 26px;
    overflow: hidden;
    box-shadow: 0 10px 28px rgba(0,0,0,.18);
  }
  .card-back {
    background: var(--green-card);
    display: flex;
    align-items: center;
    justify-content: center;
  }
  .brand {
    display: flex;
    align-items: center;
    gap: 14px;
    font-weight: 600;
    letter-spacing: 2px;
    text-transform: uppercase;
  }
  .brand-mark { border-radius: 50%; flex: none; }
  .card-back .brand { color: var(--white); font-size: 30px; }
  .card-back .brand-mark { width: 70px; height: 70px; background: var(--white); }
  .card-front { background: var(--white); }
  .card-front .swoosh { position: absolute; inset: 0; }
  .card-front .brand {
    position: absolute; top: 44px; right: 36px;
    color: var(--green-deep); font-size: 17px; gap: 10px;
  }
  .card-front .brand-mark { width: 52px; height: 52px; background: var(--grey-panel); }
  .person { position: absolute; left: 40px; top: 92px; z-index: 1; }
  .person-name { font-size: 30px; font-weight: 800; color: var(--green-deep); letter-spacing: .5px; line-height: 1.1; }
  .person-title { font-size: 15px; font-weight: 800; color: var(--green-bright); letter-spacing: .5px; line-height: 1.3; }
  .contact {
    position: absolute; left: 44px; top: 272px; z-index: 1;
    color: var(--green-deep); font-size: 14px; font-weight: 600; line-height: 19px;
    list-style: none;
  }
  .contact li { display: flex; align-items: center; gap: 8px; }
  .contact svg { width: 12px; height: 12px; flex: none; fill: var(--green-deep); }
</style>
</head>
<body>

<section class="card card-back">
  <div class="brand">
    <span class="brand-mark"></span>
    <span class="brand-name">Veldtmoor Capital Group</span>
  </div>
</section>

<section class="card card-front">
  <svg class="swoosh" viewBox="0 0 700 400" preserveAspectRatio="none" aria-hidden="true">
    <defs>
      <linearGradient id="bandGreen" x1="0" y1="0" x2="1" y2="0">
        <stop offset="0" stop-color="#3cb54a"/>
        <stop offset="1" stop-color="#0d5a2a"/>
      </linearGradient>
    </defs>
    <path d="M0,222 C200,168 520,150 625,200 C690,232 665,335 595,400 L0,400 Z" fill="url(#bandGreen)"/>
    <path d="M0,263 C200,216 480,198 580,242 C642,270 622,345 560,400 L0,400 Z" fill="var(--grey-panel)"/>
  </svg>

  <div class="brand">
    <span class="brand-mark"></span>
    <span class="brand-name">Veldtmoor Capital Group</span>
  </div>

  <div class="person">
    <h1 class="person-name">DESMOND WHITLAKE</h1>
    <p class="person-title">MANAGING PARTNER</p>
  </div>

  <ul class="contact">
    <li>187 FENWORTH ST SAN</li>
    <li>FRANCISCO, CA 94187</li>
    <li><svg viewBox="0 0 24 24"><path d="M6.6 10.8a15 15 0 0 0 6.6 6.6l2.2-2.2a1 1 0 0 1 1-.25 11.4 11.4 0 0 0 3.6.57 1 1 0 0 1 1 1V20a1 1 0 0 1-1 1A17 17 0 0 1 3 4a1 1 0 0 1 1-1h3.5a1 1 0 0 1 1 1c0 1.25.2 2.450.57 3.57a1 1 0 0 1-.25 1z"/></svg>415.555.0142</li>
    <li><svg viewBox="0 0 24 24"><path d="M6 2h10v6H6zM3 9h18v10H3zM7 14h4v2H7z"/></svg>415.555.0147</li>
    <li><svg viewBox="0 0 24 24"><path d="M7 1h10a2 2 0 0 1 2 2v18a2 2 0 0 1-2 2H7a2 2 0 0 1-2-2V3a2 2 0 0 1 2-2zm0 3v14h10V4z"/></svg>415.555.0193</li>
    <li><svg viewBox="0 0 24 24"><path d="M2 5h20v14H2zm2 2v.5l8 5 8-5V7zm0 3v7h16v-7l-8 5z"/></svg>desmond@veldtmoorcapital.ventures</li>
  </ul>
</section>

</body>
</html>
```